Business Card Design

I need business cards designed for a new company i have started that makes cakes, particularly themed kids cakes with a really modern design and I would like to have my business cards reflect this. I have attached some photos of cakes I have made and would like some to be used.

Industry/Entity Type

Business

Contact Information for Business Card

Business Name: Tarts and Treats by Maren
Mobile: 0492 815 063
email: maren@tartsandtreatsbymaren.example.au
Instagram: instagram.com/tartsandtreatsbymaren/
Facebook: fb.me/tartsandtreatsbymaren

Colors
e667a6
b768aa
3276b5

Requirements
Must have
• Business Name: Tarts and Treats by Maren
• Mobile: 0492 815 063
• email: maren@tartsandtreatsbymaren.example.au
• Instagram: instagram.com/tartsandtreatsbymaren/
• Facebook: fb.me/tartsandtreatsbymaren
Nice to have
• 2 to 3 pictures of my cakes

```html
<!DOCTYPE html>
<html lang="en">
<head>
<meta charset="utf-8">
<title>Tarts and Treats by Maren – Business Card</title>
<link rel="stylesheet" href="https://fonts.googleapis.com/css2?family=Open+Sans:wght@400;600;700&display=swap">
<style>
  :root {
    --brand-blue: #3276b5;
    --brand-pink: #e667a6;
    --brand-purple: #b768aa;
    --ink-grey: #5a5a5a;
    --card-white: #ffffff;
    --backdrop: #ecebe8;
  }
  * { box-sizing: border-box; margin: 0; padding: 0; }
  html, body { width: 1200px; height: 950px; overflow: hidden; }
  body {
    background: var(--backdrop);
    font-family: "Open Sans", Arial, sans-serif;
    display: flex;
    flex-direction: column;
    align-items: center;
    justify-content: center;
    gap: 50px;
  }
  .card {
    position: relative;
    width: 700px;
    height: 400px;
    border-radius: 4px;
    overflow: hidden;
    box-shadow: 0 6px 18px rgba(0,0,0,0.18);
  }
  .card-front {
    background: var(--brand-blue);
    display: flex;
    align-items: center;
    justify-content: center;
  }
  .wordmark {
    display: flex;
    align-items: center;
    gap: 16px;
    font-weight: 600;
    line-height: 1.05;
  }
  .wordmark-dot { width: 22px; height: 22px; border-radius: 50%; flex: none; }
  .card-front .wordmark { color: var(--card-white); font-size: 46px; }
  .card-front .wordmark-dot { background: var(--card-white); }
  .card-back { background: var(--card-white); }
  .card-back .swoosh { position: absolute; inset: 0; }
  .card-back .wordmark {
    position: absolute;
    left: 300px;
    top: 70px;
    color: var(--brand-pink);
    font-size: 38px;
  }
  .card-back .wordmark-dot { background: var(--brand-pink); width: 18px; height: 18px; }
  .contact-block { position: absolute; left: 42px; top: 222px; }
  .person-name {
    color: var(--brand-pink);
    font-weight: 700;
    font-size: 21px;
    letter-spacing: 0.5px;
    text-transform: uppercase;
  }
  .person-role { color: var(--brand-purple); font-size: 17px; margin-bottom: 10px; }
  .contact-list { list-style: none; }
  .contact-item {
    display: flex;
    align-items: center;
    gap: 12px;
    color: var(--ink-grey);
    font-size: 16px;
    line-height: 27px;
  }
  .contact-icon { width: 16px; height: 16px; flex: none; }
  .contact-square { width: 14px; height: 14px; margin: 0 1px; background: var(--brand-pink); border-radius: 2px; flex: none; }
</style>
</head>
<body>
  <section class="card card-front" aria-label="Card front">
    <div class="wordmark"><span class="wordmark-dot"></span><span>Tarts and Treats<br>by Maren</span></div>
  </section>

  <section class="card card-back" aria-label="Card back">
    <svg class="swoosh" viewBox="0 0 700 400" aria-hidden="true">
      <defs>
        <linearGradient id="bandGradient" x1="0" y1="0" x2="1" y2="1">
          <stop offset="0" stop-color="#b768aa"/>
          <stop offset="1" stop-color="#e667a6"/>
        </linearGradient>
      </defs>
      <path d="M0 0 H260 C150 40 60 120 0 240 Z" fill="url(#bandGradient)"/>
      <path d="M250 0 C140 45 55 125 0 232" fill="none" stroke="#fff" stroke-width="3"/>
      <path d="M700 110 C660 240 580 340 460 400 H700 Z" fill="url(#bandGradient)"/>
      <path d="M690 135 C650 250 575 340 470 395" fill="none" stroke="#fff" stroke-width="3"/>
    </svg>

    <div class="wordmark"><span class="wordmark-dot"></span><span>Tarts and Treats<br>by Maren</span></div>

    <div class="contact-block">
      <p class="person-name">Maren Holt</p>
      <p class="person-role">CEO/Founder</p>
      <ul class="contact-list">
        <li class="contact-item">
          <svg class="contact-icon" viewBox="0 0 16 16"><rect x="4" y="1" width="8" height="14" rx="1.5" fill="none" stroke="#e667a6" stroke-width="1.6"/><circle cx="8" cy="12.5" r="0.9" fill="#e667a6"/></svg>
          <span>0492 815 063</span>
        </li>
        <li class="contact-item">
          <svg class="contact-icon" viewBox="0 0 16 16"><rect x="1" y="3.5" width="14" height="9" rx="1" fill="#e667a6"/><path d="M1.5 4 L8 9 L14.5 4" fill="none" stroke="#fff" stroke-width="1.2"/></svg>
          <span>maren@tartsandtreatsbymaren.example.au</span>
        </li>
        <li class="contact-item"><span class="contact-square"></span><span>tartsandtreatsbymaren</span></li>
        <li class="contact-item"><span class="contact-square"></span><span>tartsandtreatsbymaren</span></li>
      </ul>
    </div>
  </section>
</body>
</html>
```